Technical Communications firm needs an article turned into a white paper

We want to redesign a 3-part blog series into a white paper that we can print for a conference. I've consolidated the three posts into the attached Word document.

We are looking for a light, easy to read design. Good use of graphics to support the message. I've added the graphics we used in the original post.

You can view them at
http://www.brightquillpages.com/blog/are-you-satisfied-with-your-dita-solution/

Target Market(s)

Product managers from High-tech, Finance, and Medical industries.

Industry/Entity Type

Information Technology

Colors

Designer to choose colors to be used in the design.

Requirements
Must have
• Must be modern, light, easy to read and slick design. Try to incorporate the graphics provided, but feel free to add more. Must retain the lists and tables.
• Must align with our website/brand.
• Must be easy to read. So not too busy.
• Please move all footnotes to endnotes. You'll need to rework the numbering.
Nice to have
• Awesome coverpage.
Should not have
• Hokey clipart. Not too heavy or hard to read.

```html
<!DOCTYPE html>
<html lang="en">
<head>
<meta charset="utf-8">
<title>Are You Satisfied With Your DITA Solution? – Part 1</title>
<link href="https://fonts.googleapis.com/css2?family=Lato:ital,wght@0,400;0,700;0,900;1,400&family=Open+Sans:ital,wght@0,400;0,600;0,700;1,400&display=swap" rel="stylesheet">
<style>
:root{
  --bg:#d9d9d6;
  --paper:#ffffff;
  --navy:#1f3d7a;
  --sky:#3b8fd0;
  --band:#4a95cf;
  --ink:#3a3a3a;
  --muted:#6a6a6a;
  --rule:#c9c9c9;
  --chalk-a:#3f6b4c;
  --chalk-b:#6a9676;
  --c-blue:#3f87c4;
  --c-green:#7ab648;
  --c-yellow:#e8b21e;
  --c-red:#c0262d;
}
*{box-sizing:border-box;margin:0;padding:0}
html,body{width:1200px;height:804px;overflow:hidden;background:var(--bg)}
body{font-family:"Open Sans",sans-serif;color:var(--ink);display:flex;align-items:center;justify-content:center}
.spread{display:flex;width:1150px;height:770px;box-shadow:0 6px 24px rgba(0,0,0,.18)}
.page{position:relative;width:575px;height:770px;background:var(--paper);display:flex;flex-direction:column;overflow:hidden}
.page--left{box-shadow:inset -14px 0 18px -14px rgba(0,0,0,.18)}
.page--right{box-shadow:inset 14px 0 18px -14px rgba(0,0,0,.18)}

.hero{height:310px;background:radial-gradient(ellipse at 55% 40%,var(--chalk-b),var(--chalk-a) 75%)}

.article-head{padding:22px 36px 0 36px;display:flex;justify-content:space-between;align-items:flex-end}
.article-title{font-family:"Lato",sans-serif;font-weight:900;font-size:25px;color:var(--navy);letter-spacing:-.3px}
.article-title span{color:var(--sky);font-weight:700}
.byline{font-family:"Lato",sans-serif;font-style:italic;font-size:12px;color:var(--muted)}
.role{text-align:right;padding:6px 36px 0;font-style:italic;font-size:8.5px;color:var(--muted)}

.body{padding:16px 36px 0;font-size:9px;line-height:1.45}
.body p{margin-bottom:9px}

.chart{display:block;margin:4px 24px 0 36px}
.chart .pct{font-family:"Lato",sans-serif;font-weight:900;font-size:19px;fill:#fff}
.chart .q{font-family:"Lato",sans-serif;font-weight:900;font-size:10.5px;fill:#fff}
.chart .rank{font-family:"Open Sans",sans-serif;font-size:9px;fill:#fff}

.footer{position:absolute;left:0;right:0;bottom:22px;height:34px;display:flex;font-size:8.5px;color:#fff}
.footer__site{background:var(--navy);display:flex;align-items:center;justify-content:center;width:150px}
.footer__contact{background:var(--band);flex:1;display:flex;align-items:center;gap:10px;padding:0 16px}
.footer__num{width:20px;height:20px;border-radius:50%;background:#fff;color:var(--navy);font-weight:700;display:flex;align-items:center;justify-content:center;font-size:9px}
.page--left .footer{padding-left:36px}
.page--left .footer__contact{justify-content:flex-start}
.page--left .footer__num{margin-left:auto}
.page--right .footer{padding-right:0}

.running-head{padding:28px 36px 0;display:flex;align-items:flex-end;gap:10px}
.running-head__title{font-size:8px;letter-spacing:1px;text-transform:uppercase;color:var(--ink);line-height:1.3;white-space:nowrap}
.running-head__rule{flex:1;height:1px;background:var(--ink);margin-bottom:4px}
.brand{display:flex;align-items:center;gap:6px;font-family:"Lato",sans-serif;font-weight:700;font-size:10px;color:var(--navy)}
.brand__dot{width:14px;height:14px;border-radius:50%;background:var(--sky)}

.section-title{font-family:"Open Sans",sans-serif;font-weight:600;font-size:19px;color:var(--sky);padding:10px 36px 6px}

.compare{margin:6px 36px 0;width:calc(100% - 72px);border-collapse:collapse;font-size:8px;line-height:1.3}
.compare th{color:#fff;font-family:"Lato",sans-serif;font-weight:700;font-size:11.5px;padding:6px 4px}
.compare th.sw{background:var(--navy)}
.compare th.sm{background:var(--sky)}
.compare td{border:1px solid var(--rule);padding:5px 6px;vertical-align:middle}
.compare td.tick{width:22px;text-align:center;font-size:10px;color:var(--ink)}
.caption{text-align:right;font-style:italic;font-size:7px;color:#9a9a9a;padding:4px 36px 0}

.checklist{list-style:none;padding:2px 36px 0;font-size:8.6px;line-height:1.4}
.checklist li{display:flex;gap:7px;margin-bottom:6px}
.checklist svg{flex:none;margin-top:1px}
</style>
</head>
<body>
<main class="spread">

  <section class="page page--left">
    <div class="hero" role="img" aria-label="Photo of a puzzled man looking up beneath chalkboard lettering reading What am I supposed to do"></div>

    <header class="article-head">
      <h1 class="article-title">Part 1: Skills <span>Development</span></h1>
      <p class="byline">By Dana Whitlow</p>
    </header>
    <p class="role">President of Brightquill Pages Authoring Solutions Inc.</p>

    <div class="body">
      <p>This article is part of a series based on the results of a survey of more than 250 technical communication professionals conducted by The Docs Corral in 2017 entitled The DITA Satisfaction Survey[i]. In the survey, almost two-thirds of respondents voiced concerns with their DITA deployment.</p>
      <p>In our previous article, we introduced the overall results from the survey that pertain to users' dissatisfaction with their DITA solution. In this article, we examine the top rated issues pertaining to skills development.</p>
      <p>Issues related to skills development</p>
      <p>The top-ranked reported issues fall under the category of skill development and training. These include</p>
    </div>

    <svg class="chart" width="500" height="190" viewBox="0 0 520 190" role="img" aria-label="Chart of top skills development issues">
      <polygon fill="var(--c-blue)" points="0,80 95,80 110,50 200,50 245,0 520,0 520,47.5 245,47.5 200,77.5 110,77.5 95,90 0,90"/>
      <polygon fill="var(--c-green)" points="0,90 95,90 110,77.5 200,77.5 245,47.5 520,47.5 520,95 245,95 200,105 110,105 95,100 0,100"/>
      <polygon fill="var(--c-yellow)" points="0,100 95,100 110,105 200,105 245,95 520,95 520,142.5 245,142.5 200,132.5 110,132.5 95,110 0,110"/>
      <polygon fill="var(--c-red)" points="0,110 95,110 110,132.5 200,132.5 245,142.5 520,142.5 520,190 245,190 200,160 110,160 95,120 0,120"/>
      <text class="pct" x="155" y="71" text-anchor="middle">75%</text>
      <text class="pct" x="155" y="98" text-anchor="middle">69%</text>
      <text class="pct" x="155" y="126" text-anchor="middle">64%</text>
      <text class="pct" x="155" y="153" text-anchor="middle">56%</text>
      <text class="q" x="258" y="20">HOW DO I REUSE CONTENT?</text>
      <text class="rank" x="258" y="34">Ranked 1st by 75% of respondents</text>
      <text class="q" x="258" y="64">HOW DO I MAKE DITA DO WHAT I</text>
      <text class="q" x="258" y="75">WANT IT TO DO?</text>
      <text class="rank" x="258" y="88">Ranked 1st by 75% of respondents</text>
      <text class="q" x="258" y="116">WHERE CAN I GET DITA TRAINING?</text>
      <text class="rank" x="258" y="130">Ranked 3rd by 64% of respondents</text>
      <text class="q" x="258" y="163">HOW DO I CREATE DITA CONTENT?</text>
      <text class="rank" x="258" y="177">Ranked 8th by 56% of respondents</text>
    </svg>

    <footer class="footer">
      <div class="footer__site">www.brightquillpages.com</div>
      <div class="footer__contact">
        <span>+1 (555) 014-2290, Press 1#</span><span>|</span><span>support-desk@brightquillpages.com</span>
        <span class="footer__num">8</span>
      </div>
    </footer>
  </section>

  <section class="page page--right">
    <header class="running-head">
      <p class="running-head__title">Are you satisfied<br>with your DITA solution?</p>
      <span class="running-head__rule"></span>
      <div class="brand"><span class="brand__dot"></span>Brightquill Pages</div>
    </header>

    <div class="body">
      <p>This problem area is far and away the most pressing obstacle for a successful DITA deployment. Too often authors are left to figure out how to adapt to writing for DITA on their own. Organizations will normally invest in tools training—and may even opt for a short training course to learn about DITA—but they rarely make the effort to train writers how to author modular, structured topics of content designed for reuse. It is easy to overlook this training aspect and assume that writers will naturally adapt to this new way of writing. But, those assumptions can lead to big problems.</p>
      <p>In a poll conducted in a recent webinar[ii] where half of the participants indicated they were already using DITA, a full 70% indicated that they had no formal DITA training. Of those participants, nearly 60% were self-taught while the others had no training at all. It's no wonder that dissatisfaction is the norm.</p>
    </div>

    <h2 class="section-title">Selecting the best training for your needs</h2>
    <div class="body" style="padding-top:0">
      <p>There are many training options available to learn about DITA. Selecting the best training for your team entails examining what it is you need to learn. Most DITA training courses cover the features and walk you through the structures and mechanics of the standard. These courses demonstrate how to markup content, but will often not teach you how to rethink and restructure your content to take advantage of DITA's features. Consider the differences between structured writing and structured markup.</p>
    </div>

    <table class="compare">
      <thead><tr><th class="sw" colspan="2">Structured Writing</th><th class="sm" colspan="2">Structured Markup</th></tr></thead>
      <tbody>
        <tr><td class="tick">✓</td><td>Coined by Martin Hale in the 1960's as a means of analyzing, organizing, and presenting information for optimal human consumption</td><td class="tick">✓</td><td>Allows authors to markup words, phrases, and sections of content for presentation and for meaning for consumption by machines</td></tr>
        <tr><td class="tick">✓</td><td>Promotes patterns for format and syntax that become easily recognizable and predictable</td><td class="tick">✓</td><td>Is validated using standard sets of rules that specify consistent and predictable patterns</td></tr>
        <tr><td class="tick">✓</td><td>Relies on consistently labelling and chunking information into easily scannable text</td><td class="tick">✓</td><td>Specifies what content goes where but does not limit or restrict how the content is written</td></tr>
        <tr><td class="tick">✓</td><td>Introduces universal information typing based on intended reader response</td><td class="tick">✓</td><td>Provides a rich underlying metadata layer for capturing properties related to the content</td></tr>
      </tbody>
    </table>
    <p class="caption">Table reproduced from "Driving Enterprise Productivity from the Front of the DITA XML Train[iii]".</p>

    <h2 class="section-title">Continuous collaborative learning</h2>
    <div class="body" style="padding-top:0">
      <p>Organizations that wisely invest in comprehensive training for their writing teams also recognize the importance of continuous learning and recurring training. To stay on top of knowledge sharing in your team, consider the following collaboration activities:</p>
    </div>
    <ul class="checklist">
      <li><svg width="10" height="10" viewBox="0 0 10 10"><rect x=".5" y=".5" width="9" height="9" fill="none" stroke="#3a3a3a"/><path d="M2 5l2 2 4-5" fill="none" stroke="#3a3a3a" stroke-width="1.3"/></svg>Schedule regular checkpoints where your team discusses what they've learned with other members of the team.</li>
      <li><svg width="10" height="10" viewBox="0 0 10 10"><rect x=".5" y=".5" width="9" height="9" fill="none" stroke="#3a3a3a"/><path d="M2 5l2 2 4-5" fill="none" stroke="#3a3a3a" stroke-width="1.3"/></svg>Assign different members of your team to research and present best practices at regularly scheduled lunch-and-learn sessions.</li>
      <li><svg width="10" height="10" viewBox="0 0 10 10"><rect x=".5" y=".5" width="9" height="9" fill="none" stroke="#3a3a3a"/><path d="M2 5l2 2 4-5" fill="none" stroke="#3a3a3a" stroke-width="1.3"/></svg>Attend webinars and seminars on best practices as a group and then debrief together to discuss aspects that should be incorporated into your day-to-day work.</li>
      <li><svg width="10" height="10" viewBox="0 0 10 10"><rect x=".5" y=".5" width="9" height="9" fill="none" stroke="#3a3a3a"/><path d="M2 5l2 2 4-5" fill="none" stroke="#3a3a3a" stroke-width="1.3"/></svg>Review and update your content standards regularly as a team to keep your procedures and guidelines current and relevant.</li>
      <li><svg width="10" height="10" viewBox="0 0 10 10"><rect x=".5" y=".5" width="9" height="9" fill="none" stroke="#3a3a3a"/><path d="M2 5l2 2 4-5" fill="none" stroke="#3a3a3a" stroke-width="1.3"/></svg>Pair up senior members of your team with new or junior members for regular mentoring and coaching.</li>
    </ul>

    <footer class="footer">
      <div class="footer__contact">
        <span class="footer__num">9</span>
        <span>+1 (555) 014-2290, Press 1#</span><span>|</span><span>support-desk@brightquillpages.com</span>
      </div>
      <div class="footer__site">www.northleafprint.com</div>
    </footer>
  </section>

</main>
</body>
</html>
```